Creation of a construction/bricklaying business website

Following the template format of "Halloway 7", the following content would need to be included:
1. Landing page with 3 tiles that go to their own pages.
- Landing page to include background photo and description of services offered.
2. 3 tiles to include:
a) "Contact Us For A Free Quote or Friendly Discussion" Form (middle tile)
b) Case Studies and Testimonials
c) Certifications and Professional Membership
- Design logo to be used from previous SketchNestle project. Example of logo attached below, please access full JPG files from our account.

Target Market(s)

Prospective clients seeking construction work (bricklaying speciality)

Industry/Entity Type

Residential Construction

Coding

Coded - Design and coding required

Number of Pages Required

4 page

Font styles to use
Sans Serif

Colors

Designer to choose colors to be used in the design.

Requirements
Must have
• Following the template format of "Halloway 7", the following content would need to be included:
• 1. Landing parent page with 3 tiles that go to the 3 child pages.
• - Landing page to include background photo and description of services offered.
• 2. 3 tiles to include:
• a) "Contact Us For A Free Quote or Friendly Discussion" Form (middle tile)
• b) Case Studies and Testimonials (first tile / left side)
• c) Certifications and Professional Memberships (third tile / right side) (This should include logos of the relevant organisations being displayed. Specifically GQT and the Pillar Seal GQT).
• - Design logo to be used from previous SketchNestle project. Example of logo attached below, please access full JPG files from our account.
Nice to have
• Sleek and modern feel.
• Approachable in terms of how people can contact the company for a quote.
• Traditional pictures to give credibility and comfort around choosing this company.
Should not have
• Cheesy pictures
• Over-complicated
• Simple to use
• Easy URL domain name

```html
<!DOCTYPE html>
<html lang="en">
<head>
<meta charset="utf-8">
<title>R.T.Hale Construction Ltd</title>
<link href="https://fonts.googleapis.com/css2?family=Exo+2:wght@500;600&family=Jost:wght@400;500&display=swap" rel="stylesheet">
<style>
:root{
  --brand-blue:#0c56a6;
  --brand-blue-deep:#0b52a0;
  --hero-dark:#2b2622;
  --tile-grey:#e8ecec;
  --ink:#111;
  --white:#fff;
  --icon-grey:#6b6b6b;
  --badge-red:#c8102e;
  --rule:rgba(255,255,255,.25);
}
*{box-sizing:border-box;margin:0;padding:0}
html,body{width:1034px;height:1200px;overflow:hidden;background:var(--white)}
body{font-family:"Jost",sans-serif;color:var(--ink);position:relative}

/* hero */
.hero{position:absolute;left:0;top:0;width:1034px;height:505px;overflow:hidden}
.hero-photo{position:absolute;inset:0;
  background:
    linear-gradient(rgba(20,18,16,.55),rgba(20,18,16,.55)),
    radial-gradient(ellipse at 50% 30%,#5a5652 0%,#3a3530 45%,transparent 70%),
    linear-gradient(180deg,#2f3a2c 0%,#4a3a30 40%,#5b3a2a 70%,#2e3a26 100%);}
.top-contact{position:absolute;top:18px;display:flex;align-items:center;gap:8px;color:var(--white);font-size:12px;line-height:19px}
.top-contact.phone{left:140px}
.top-contact.email{left:706px}
.round-icon{width:32px;height:32px;border-radius:50%;background:var(--brand-blue);display:flex;align-items:center;justify-content:center;flex:none}
.hero-brand{position:absolute;top:112px;left:0;width:100%;text-align:center;font-family:"Exo 2",sans-serif;font-weight:600;font-size:52px;color:#1a5aa8;opacity:.85}
.hero-title{position:absolute;top:236px;left:0;width:100%;text-align:center;font-family:"Exo 2",sans-serif;font-weight:500;font-size:23px;line-height:28px;color:var(--white)}
.services{position:absolute;top:306px;left:0;width:100%;text-align:center;font-family:"Exo 2",sans-serif;font-weight:500;font-size:17px;line-height:19px;color:var(--white)}
.services span{margin:0 14px}
.services span::before{content:"\2022";margin-right:14px}
.cta{position:absolute;top:372px;left:447px;width:139px;height:28px;background:var(--brand-blue);color:var(--white);font-size:14px;display:flex;align-items:center;justify-content:center;gap:6px}

/* intro */
.intro-brand{position:absolute;top:552px;left:0;width:100%;text-align:center;font-family:"Jost",sans-serif;font-weight:500;font-size:22px;color:var(--brand-blue)}
.intro-text{position:absolute;top:601px;left:140px;width:754px;text-align:center;font-size:13.2px;line-height:21px}
.intro-text p+p{margin-top:7px}

/* tiles */
.tiles{position:absolute;top:722px;left:140px;width:754px;height:220px;display:flex}
.tile{flex:1;text-align:center;padding:24px 8px 0}
.tile.shaded{background:var(--tile-grey)}
.tile-icon{width:60px;height:54px;margin:0 auto 14px}
.tile-title{font-family:"Exo 2",sans-serif;font-weight:600;font-size:12.5px;line-height:16px;margin-bottom:14px}
.tile-body{font-size:12px;line-height:18px}
.badges{display:flex;gap:6px;justify-content:center;margin-bottom:14px}
.badge{width:32px;height:54px;background:var(--badge-red)}

/* footer */
.footer{position:absolute;top:984px;left:0;width:1034px;height:216px;background:var(--brand-blue-deep);color:var(--white)}
.footer-brand{position:absolute;top:28px;left:0;width:100%;text-align:center;font-weight:500;font-size:24px}
.footer-contact{position:absolute;top:90px;display:flex;align-items:center;gap:10px;font-size:12.5px;line-height:19px}
.footer-contact .round-icon{background:var(--icon-grey)}
.footer-contact.address{left:164px}
.footer-contact.phone{left:441px}
.footer-contact.email{left:670px}
.footer-rule{position:absolute;top:145px;left:164px;width:696px;height:1px;background:var(--rule)}
.copyright{position:absolute;top:170px;left:164px;font-size:12.5px}
.social{position:absolute;top:164px;left:744px;display:flex;gap:4px}
.social span{width:26px;height:26px;border-radius:50%;background:var(--white)}
</style>
</head>
<body>

<header class="hero">
  <div class="hero-photo" role="img" aria-label="Photo of a finished brick garden wall and paved patio"></div>

  <div class="top-contact phone">
    <span class="round-icon"><svg width="16" height="16" viewBox="0 0 24 24"><path fill="#fff" d="M6.6 10.8a15.1 15.1 0 006.6 6.6l2.2-2.2a1 1 0 011-.25 11.4 11.4 0 003.6.57 1 1 0 011 1V20a1 1 0 01-1 1A17 17 0 013 4a1 1 0 011-1h3.5a1 1 0 011 1c0 1.25.2 2.45.57 3.6a1 1 0 01-.25 1z"/></svg></span>
    <span>Call Us On :<br>123.456.7890</span>
  </div>
  <div class="top-contact email">
    <span class="round-icon"><svg width="16" height="12" viewBox="0 0 16 12"><rect x="0.5" y="0.5" width="15" height="11" fill="none" stroke="#fff"/><path d="M0.5 0.5L8 7l7.5-6.5" fill="none" stroke="#fff"/></svg></span>
    <span>Email<br>info@rthaleconstruction.com</span>
  </div>

  <div class="hero-brand">R.T.Hale Construction Ltd</div>

  <h1 class="hero-title">R.T.Hale Construction Ltd is a construction company that<br>has expertise and experience in the following areas</h1>

  <div class="services">
    <div><span>Extensions</span><span>New build / New houses</span><span>Garden walls</span></div>
    <div><span>Plastering</span><span>Brickwork</span><span>Groundworks</span></div>
  </div>

  <div class="cta">Contact Us Today <svg width="14" height="8" viewBox="0 0 14 8"><path d="M0 4h12M9 1l3 3-3 3" fill="none" stroke="#fff"/></svg></div>
</header>

<section>
  <div class="intro-brand">R.T.Hale</div>
  <div class="intro-text">
    <p>We pride ourselves on attention to detail, pride in our completed project and client satisfaction. We believe in full transparency and this is reflected in the jobs we quote for you. We break down each step with both labour and materials cost so you can see exactly what you are paying for.</p>
    <p>Feel free to get in touch and we can talk through what you are looking to achieve.</p>
  </div>

  <div class="tiles">
    <div class="tile shaded">
      <div class="tile-icon" role="img" aria-label="Case study document icon" style="background:linear-gradient(135deg,#1d5aa6,#8a8f96);border-radius:4px"></div>
      <div class="tile-title">Case Studies and<br>Testimonials</div>
      <div class="tile-body">Ut wisi enim ad minim veniam, quis nostrud exerci tation ullamcorper suscipit lobortis nisl ut aliquip ex ea commodo consequat.</div>
    </div>
    <div class="tile">
      <div class="tile-icon" role="img" aria-label="Quote request form icon" style="width:46px;background:linear-gradient(135deg,#1d5aa6,#153f7a);border-radius:4px"></div>
      <div class="tile-title">Contact Us For A<br>Free Quote</div>
      <div class="tile-body">Ut wisi enim ad minim veniam, quis nostrud exerci tation ullamcorper suscipit lobortis nisl ut aliquip ex ea commodo consequat.</div>
    </div>
    <div class="tile shaded">
      <div class="badges">
        <span class="badge" role="img" aria-label="Membership badge"></span>
        <span class="badge" role="img" aria-label="Pillar Seal GQT badge"></span>
      </div>
      <div class="tile-title">Certifications and Professional<br>Memberships</div>
      <div class="tile-body">Ut wisi enim ad minim veniam, quis nostrud exerci tation ullamcorper suscipit lobortis nisl ut aliquip ex ea commodo consequat.</div>
    </div>
  </div>
</section>

<footer class="footer">
  <div class="footer-brand">R.T.Hale</div>

  <div class="footer-contact address">
    <span class="round-icon"><svg width="12" height="16" viewBox="0 0 12 16"><path fill="#fff" d="M6 0a6 6 0 00-6 6c0 4.5 6 10 6 10s6-5.5 6-10a6 6 0 00-6-6zm0 8.2A2.2 2.2 0 116 3.8a2.2 2.2 0 010 4.4z"/></svg></span>
    <span>Street Name, City Name<br>State Zipcode</span>
  </div>
  <div class="footer-contact phone">
    <span class="round-icon"><svg width="16" height="16" viewBox="0 0 24 24"><path fill="#fff" d="M6.6 10.8a15.1 15.1 0 006.6 6.6l2.2-2.2a1 1 0 011-.25 11.4 11.4 0 003.6.57 1 1 0 011 1V20a1 1 0 01-1 1A17 17 0 013 4a1 1 0 011-1h3.5a1 1 0 011 1c0 1.25.2 2.45.57 3.6a1 1 0 01-.25 1z"/></svg></span>
    <span>Call Us On :<br>123.456.7890</span>
  </div>
  <div class="footer-contact email">
    <span class="round-icon"><svg width="16" height="12" viewBox="0 0 16 12"><rect x="0.5" y="0.5" width="15" height="11" fill="none" stroke="#fff"/><path d="M0.5 0.5L8 7l7.5-6.5" fill="none" stroke="#fff"/></svg></span>
    <span>Email<br>info@rthaleconstruction.com</span>
  </div>

  <div class="footer-rule"></div>
  <div class="copyright">Copyright ©2018 R.T.Hale Construction Ltd. All Rights Reserved.</div>
  <div class="social"><span></span><span></span><span></span><span></span></div>
</footer>

</body>
</html>
```